New Website Design for PHOVAN.org

We are looking for a new website design for PHOVAN.org. PHOVAN is a non profit home inspector association based in California. Home Inspectors are people that come out and look at a house before it's purchased to let the buyer know of any defects that may exist.
Our site is based on Joomla so if you'll be able to make a Joomla 3 template as well, please let us know (not required, but a bonus).
We would like to see designs that incorporate royal blue, white and chrome into the site as that's our main business colors.
We would like a place for rotating banners though they don't need to be the same size as the current site.
We would like navigation to be easier to manage with menus only across the top (via drop down menus) where we are going to sort out the items currently on the side. Possibly the front page could have a graphic link to separate portals for Realtors, Home Buyers and Inspectors, but that's just one option.
We would like a good mobile design or something that will scale easily to mobile.
The Find an Inspector feature is important and should stand out. The ASK PHOVANr site
Current home page feels a bit busy. Would like to simplify a bit.

```html
<!DOCTYPE html>
<html lang="en">
<head>
<meta charset="utf-8">
<title>PHOVAN – Home</title>
<link href="https://fonts.googleapis.com/css2?family=Open+Sans:ital,wght@0,400;0,600;0,700;1,400&family=Cinzel:wght@600&display=swap" rel="stylesheet">
<style>
:root{
  --royal:#1f1fd6;
  --accent:#6a5aa8;
  --accent-dark:#4d3f8c;
  --ink:#333;
  --body:#444;
  --muted:#888;
  --line:#e2e2e2;
  --dots:#c8c8c8;
  --footer:#2b2b2b;
  --bg:#fff;
}
*{box-sizing:border-box;margin:0;padding:0}
html,body{width:1109px;height:1200px;overflow:hidden;background:var(--bg)}
body{font-family:"Open Sans",Arial,sans-serif;color:var(--body)}
.page{position:relative;width:1200px;height:1299px;transform:scale(.924167);transform-origin:0 0}
.abs{position:absolute}

/* header */
.brand{left:120px;top:10px;display:flex;align-items:center;gap:24px}
.brand-mark{width:90px;height:90px;border-radius:50%;background:#e8e8f0;border:3px solid #9aa0c0}
.brand-name{font-weight:700;font-size:27px;line-height:29px;color:var(--royal);letter-spacing:.5px}
.contact{right:130px;top:10px;font-size:19px;line-height:27px;color:#222}
.contact span{color:var(--accent-dark);display:inline-block;width:62px}
.social{right:132px;top:70px;display:flex;gap:8px}
.social i{width:25px;height:25px;border:1px solid #ccc;border-radius:3px;background:linear-gradient(#fafafa,#e4e4e4)}

/* nav */
.nav{left:120px;top:118px;width:961px;height:52px;border:1px solid #eee;border-bottom:none;display:flex;align-items:center;padding-left:10px}
.nav a{font-size:13.5px;color:#444;text-decoration:none;margin-right:29px}
.nav a.active{color:var(--accent-dark)}
.search{right:131px;top:131px;width:227px;height:26px;border:1px solid #e4e4e4;border-radius:3px;font-size:12px;color:#aaa;padding:5px 6px;background:#fafafa}
.search svg{position:absolute;right:6px;top:4px}

/* hero */
.hero{left:120px;top:170px;width:961px;height:362px;background:linear-gradient(100deg,#4d6236 0%,#6b7a55 35%,#555a5c 55%,#8a4d3a 75%,#6d7a54 100%)}
.hero-box{left:120px;top:250px;width:362px;height:202px;background:rgba(30,30,30,.72);padding:10px 17px}
.hero-title{font-family:"Cinzel",serif;font-size:26px;line-height:34px;color:#fff;letter-spacing:1px}
.hero-text{font-size:14px;line-height:21.5px;color:#e6e6e6;margin-top:6px;letter-spacing:-.3px}
.btn{display:inline-block;background:var(--accent);color:#fff;border:1px solid var(--accent-dark);border-radius:2px;font-size:14px;padding:4px 7px}
.hero-box .btn{margin-top:13px}

/* section headings */
.heading{display:flex;align-items:center;gap:12px;font-size:23px;color:var(--ink)}
.heading::after{content:"";flex:1;border-top:3px dotted var(--dots);margin-top:4px}
.heading em{font-style:normal;color:var(--accent-dark)}

.welcome{left:130px;top:562px;width:662px}
.welcome p{font-size:12.3px;line-height:22px;color:#333;margin-top:6px}
.welcome p+p{margin-top:21px}
.welcome .btn{margin-top:9px;border-radius:3px;padding:5px 7px}

.login{left:837px;top:566px;width:231px}
.login .heading{font-size:20px}
.login label{display:block;font-size:11px;color:var(--muted);margin-top:16px;margin-left:3px}
.login label+label{margin-top:8px}
.field{width:224px;height:28px;border:1px solid #ddd;margin:4px 0 0 4px;box-shadow:inset 0 1px 2px #eee}
.login-row{display:flex;justify-content:space-between;align-items:center;margin-top:30px}
.login-row .btn{width:70px;text-align:center;font-size:13px;font-weight:600;padding:3px 0;margin-left:2px;background:linear-gradient(#7a6cb6,#5a4b98)}
.login-row a{font-size:11.5px;color:var(--accent-dark);margin-right:8px}

.projects{left:130px;top:800px;width:937px}
.tiles{left:130px;top:835px;display:flex;gap:16px}
.tile{width:223px;height:126px;border:1px solid #e6e6e6}

.software{left:130px;top:994px;width:451px}
.acc{left:130px;top:1036px;width:451px}
.acc li{list-style:none;height:55px;border-bottom:1px solid var(--line);display:flex;align-items:center;gap:8px;font-size:16.5px;color:#333;padding-bottom:4px}
.acc li:first-child{height:36px;margin-bottom:0}
.plus{width:20px;height:20px;border-radius:50%;background:var(--accent);color:#fff;font-size:17px;line-height:19px;text-align:center;font-weight:700}

.testi{left:607px;top:994px;width:462px}
.arrows{right:131px;top:1000px;display:flex;gap:5px}
.arrows span{width:16px;height:16px;border-radius:50%;background:#555;display:flex;align-items:center;justify-content:center}
.quote{left:607px;top:1038px;width:462px;height:152px;border:1px solid #ddd;border-radius:2px;background:#fafafa;padding:14px 24px 0 46px;font-style:italic;font-size:13.5px;line-height:20px;color:#888}
.quote::before{content:"\201C";position:absolute;left:25px;top:6px;font-size:34px;color:var(--accent);font-style:normal}
.avatar{left:609px;top:1200px}
.author{right:132px;top:1211px;font-size:13px;color:var(--accent)}

.footer{left:0;top:1256px;width:1200px;height:43px;background:var(--footer);color:#ccc;font-size:11.5px;display:flex;justify-content:space-between;align-items:center;padding:0 132px 0 130px}
</style>
</head>
<body>
<div class="page">
  <header>
    <div class="abs brand">
      <div class="brand-mark"></div>
      <div class="brand-name">PACIFIC HOME VERIFICATION<br>&nbsp;&nbsp;&nbsp;&nbsp;&nbsp;ASSOCIATION</div>
    </div>
    <div class="abs contact">
      <div><span>Phone:</span>(800) 555-0142</div>
      <div><span>Fax:</span>&nbsp;(916) 555-0178</div>
    </div>
    <div class="abs social"><i></i><i></i><i></i><i></i></div>
  </header>

  <nav class="abs nav">
    <a class="active">Home</a><a>Find an Inspector</a><a>Home Buyers &amp; Sellers</a><a>Real Estate Agents</a><a>Inspectors</a><a>Ask Phovan</a>
  </nav>
  <div class="abs search">Search...
    <svg width="18" height="18" viewBox="0 0 18 18"><circle cx="7" cy="7" r="5" fill="none" stroke="#bbb" stroke-width="2"/><line x1="11" y1="11" x2="16" y2="16" stroke="#bbb" stroke-width="3"/></svg>
  </div>

  <div class="abs hero" role="img" aria-label="Inspector writing notes on a clipboard beside a brick porch pillar"></div>
  <div class="abs hero-box">
    <div class="hero-title">PACIFIC HOME VERIFICATION ASSOCIATION</div>
    <p class="hero-text">Contrairement à une opinion répandue, le Lorem Ipsum n'est pas simplement du texte aléatoire. Ses racines dans une littérature latine classique datant.</p>
    <span class="btn">Know More</span>
  </div>

  <section class="abs welcome">
    <h2 class="heading">Welcome To&nbsp;<em>PHOVAN</em></h2>
    <p>Contrairement à une opinion répandue, le Lorem Ipsum n'est pas simplement du texte aléatoire. Il trouve ses racines dans une oeuvre de la littérature latine classique datant deContrairement à une opinion répandue. Lorem Ipsum n'est pas simplement du texte aléatoire.</p>
    <p>Contrairement à une opinion répandue, Latine classique datant. Il trouve ses racines dans une oeuvre de la littérature latine classique datant deContrairement à une opinion répandue.</p>
    <span class="btn">READ MORE</span>
  </section>

  <aside class="abs login">
    <h2 class="heading">Inspector Login</h2>
    <label>User Name</label><div class="field"></div>
    <label>Password</label><div class="field"></div>
    <div class="login-row"><span class="btn">Login</span><a>Forgot Login?</a></div>
  </aside>

  <h2 class="abs heading projects">Recent Projects</h2>
  <div class="abs tiles">
    <div class="tile" role="img" aria-label="Inspector in hard hat checking a window frame" style="background:linear-gradient(90deg,#a98050,#8fa7c4 45%,#6c8cb8)"></div>
    <div class="tile" role="img" aria-label="Open books stacked on a table" style="background:linear-gradient(#6b4a2a,#c9a878 60%,#8a5e34)"></div>
    <div class="tile" role="img" aria-label="Figure leaning on a red question mark" style="background:radial-gradient(circle at 50% 50%,#e0a0a0,#fff 60%)"></div>
    <div class="tile" role="img" aria-label="Online store banner" style="background:linear-gradient(90deg,#f4f4f4,#fbe7d8)"></div>
  </div>

  <h2 class="abs heading software">Home Inspection Software</h2>
  <ul class="abs acc">
    <li><span class="plus">+</span>California Real Estate Inspection Law</li>
    <li><span class="plus">+</span>PHOVAN Chapter Meeting Locations</li>
    <li><span class="plus">+</span>Standard Of Practice</li>
    <li><span class="plus">+</span>Code Of Ethics</li>
  </ul>

  <h2 class="abs heading testi" style="width:418px">Testimonials</h2>
  <div class="abs arrows">
    <span><svg width="8" height="8" viewBox="0 0 8 8"><path d="M6 0L1 4l5 4z" fill="#fff"/></svg></span>
    <span><svg width="8" height="8" viewBox="0 0 8 8"><path d="M2 0l5 4-5 4z" fill="#fff"/></svg></span>
  </div>
  <blockquote class="abs quote">Lorem ipsum dolor sit amet, consectetur adipisicing elit, sed do eiusmod tempor incididunt ut labore et dolore magna aliqua. Ut enim ad minim veniam, quis nostrud exercitation ullamco laboris nisi ut aliquip ex ea commodo consequat. Duis aute irure dolor in reprehenderit in voluptate velit esse cillum dolore eu fugiat nulla pariatur.</blockquote>
  <svg class="abs avatar" width="34" height="36" viewBox="0 0 34 36" aria-hidden="true"><circle cx="17" cy="10" r="8" fill="#aaa"/><path d="M1 35c0-10 7-15 16-15s16 5 16 15z" fill="#aaa"/></svg>
  <div class="abs author">Marlon Ashby</div>

  <footer class="abs footer">
    <span>Copyright © 2013 &nbsp;All Rights Reserved</span>
    <span>Terms &amp; Condition &nbsp;| &nbsp;Privacy Policy</span>
  </footer>
</div>
</body>
</html>
```